Structural Engineering Business Card

Brookvane Drafting does residential house plans for clients in Central Florida. Would like simple but elegant business card that is appropriate for a house plan engineering company. Prefer black business card with black/white them but open to other shades of blue. I uploaded a sample card that I came across that looked good but please come up with your own creative designs.

Contact Information for Business Card

Name, Title, Phone, Email, Address, website

```html
<!DOCTYPE html>
<html lang="en">
<head>
<meta charset="utf-8">
<title>Brookvane Drafting – Business Card</title>
<link href="https://fonts.googleapis.com/css2?family=Montserrat:wght@700;800&family=Lato:wght@300;400&display=swap" rel="stylesheet">
<style>
  :root {
    --backdrop: #2a2b2e;
    --card-deep: #060b16;
    --card-navy: #0c1a36;
    --teal: #1fa99c;
    --white: #ffffff;
    --soft-white: #dfe6ee;
  }
  * { margin: 0; padding: 0; box-sizing: border-box; }
  html, body {
    width: 1200px; height: 817px; overflow: hidden;
    background: var(--backdrop);
  }
  .canvas {
    position: relative; width: 1200px; height: 817px;
    display: flex; align-items: center; justify-content: center; gap: 40px;
  }
  .card {
    position: relative; width: 540px; height: 309px;
    border-radius: 26px; overflow: hidden;
    background: linear-gradient(135deg, var(--card-navy) 0%, var(--card-deep) 70%);
    box-shadow: 0 18px 40px rgba(0,0,0,0.45);
  }
  .blueprint-art {
    position: absolute; inset: 0;
  }
  .card-front .blueprint-art {
    background: radial-gradient(ellipse 70% 60% at 65% 95%, rgba(31,169,156,0.16) 0%, rgba(18,58,74,0.10) 45%, rgba(18,58,74,0) 100%);
  }
  .card-back .blueprint-art {
    background: radial-gradient(ellipse 65% 80% at 85% 35%, rgba(31,169,156,0.14) 0%, rgba(18,58,74,0.10) 45%, rgba(18,58,74,0) 100%);
  }

  .identity { position: absolute; left: 36px; top: 128px; }
  .identity-name {
    font-family: "Montserrat", sans-serif; font-weight: 800;
    font-size: 21px; letter-spacing: 0.4px; color: var(--white);
    text-transform: uppercase; white-space: nowrap;
  }
  .identity-title {
    font-family: "Lato", sans-serif; font-weight: 300;
    font-size: 18px; color: var(--soft-white); margin-top: 2px;
  }
  .identity-rule { width: 84px; height: 2px; background: var(--teal); margin-top: 10px; }

  .contact-list {
    position: absolute; right: 28px; top: 38px;
    list-style: none; text-align: right;
    font-family: "Lato", sans-serif; font-weight: 400;
    font-size: 12px; line-height: 1.35; color: var(--soft-white);
  }
  .contact-item { display: flex; justify-content: flex-end; align-items: flex-start; gap: 10px; margin-bottom: 9px; }
  .contact-icon {
    flex: 0 0 18px; width: 18px; height: 18px; border-radius: 3px;
    background: var(--teal); display: flex; align-items: center; justify-content: center;
  }
  .contact-icon svg { width: 12px; height: 12px; }

  .brand-name {
    position: absolute; left: 70px; bottom: 70px;
    font-family: "Montserrat", sans-serif; font-weight: 800;
    font-size: 40px; line-height: 1.05; color: var(--white);
    text-transform: uppercase; letter-spacing: 1px;
  }
</style>
</head>
<body>
<main class="canvas">
  <article class="card card-front">
    <div class="blueprint-art" role="img" aria-label="Faint teal blueprint line drawing of a house elevation"></div>
    <div class="identity">
      <h1 class="identity-name">Daniel R. Whitmore</h1>
      <p class="identity-title">Managing Director</p>
      <div class="identity-rule"></div>
    </div>
    <ul class="contact-list">
      <li class="contact-item">
        <span>2715 Harbor Pine Avenue<br>Florida, U.S. 32801</span>
        <span class="contact-icon"><svg viewBox="0 0 12 12"><path d="M6 1a3.5 3.5 0 0 0-3.5 3.5C2.5 7 6 11 6 11s3.5-4 3.5-6.5A3.5 3.5 0 0 0 6 1zm0 4.8A1.3 1.3 0 1 1 6 3.2a1.3 1.3 0 0 1 0 2.6z" fill="#fff"/></svg></span>
      </li>
      <li class="contact-item">
        <span>+1 407 555 0148</span>
        <span class="contact-icon"><svg viewBox="0 0 12 12"><path d="M3.2 1.5l1.6 2.2-.9 1.1a6 6 0 0 0 3.3 3.3l1.1-.9 2.2 1.6-.7 1.6C6 10.3 1.7 6 1.6 2.2z" fill="#fff"/></svg></span>
      </li>
      <li class="contact-item">
        <span>hello@brookvanedrafting.com</span>
        <span class="contact-icon"><svg viewBox="0 0 12 12"><rect x="1.5" y="3" width="9" height="6" fill="none" stroke="#fff" stroke-width="1"/><path d="M1.5 3L6 6.5 10.5 3" fill="none" stroke="#fff" stroke-width="1"/></svg></span>
      </li>
      <li class="contact-item">
        <span>www.brookvanedrafting.com</span>
        <span class="contact-icon"><svg viewBox="0 0 12 12"><path d="M3 2l6.5 3.2-2.7.8 1.9 3-1.2.7-1.8-3-2 1.9z" fill="#fff"/></svg></span>
      </li>
    </ul>
  </article>

  <article class="card card-back">
    <div class="blueprint-art" role="img" aria-label="Faint teal blueprint line drawing of a house gable and windows"></div>
    <p class="brand-name">Brookvane<br>Drafting</p>
  </article>
</main>
</body>
</html>
```